Business Card for my New Brokerage

Looking to get a business card design for my new Real Estate Brokerage.
I want it with Picture, Phone Number, Email, Website, Office Address
Name and Designation. Please add logo too.

Target Market(s)

Real Estate Investors or Home Buyers

Industry/Entity Type

Real Estate

Contact Information for Business Card

Name, Email, Phone Number, website, email, office address

Colors
EB3D1F
EC4F4E
F09395
F8D3D4
FCEDEE

Requirements
Must have
• Minimalistic, Clean, Modern, Photo
Nice to have
• White and Red Colors

```html
<!DOCTYPE html>
<html lang="en">
<head>
<meta charset="utf-8">
<title>Ember Realty Inc — Business Card</title>
<link rel="stylesheet" href="https://fonts.googleapis.com/css2?family=Open+Sans:wght@600;700&family=Source+Sans+3:wght@400&display=swap">
<style>
  :root {
    --brand-red: #dd1f26;
    --card-red-top: #de3a41;
    --card-red-bottom: #be1a22;
    --gold: #ead38e;
    --white: #ffffff;
    --paper: #ffffff;
    --sky: #f6f6f6;
    --land-mid: #8e8e8e;
    --land-dark: #262626;
  }
  * { box-sizing: border-box; margin: 0; padding: 0; }
  html, body {
    width: 927px; height: 1200px; overflow: hidden;
    background: var(--paper);
  }
  .sheet { position: relative; width: 927px; height: 1200px; }
  .card {
    position: absolute; left: 64px; width: 792px; height: 452px;
    box-shadow: 0 2px 8px rgba(0,0,0,0.22);
    overflow: hidden;
  }
  .card--front { top: 111px; background: var(--brand-red); }
  .card--back { top: 628px; }

  .front__photo {
    position: absolute; left: 15px; right: 15px; top: 0; bottom: 0;
    background: linear-gradient(180deg, var(--sky) 0%, #e6e6e6 38%, var(--land-mid) 55%, #5c5c5c 75%, var(--land-dark) 100%);
  }
  .company-name {
    position: absolute; left: 0; right: 0; top: 120px;
    text-align: center;
    font-family: "Open Sans", sans-serif; font-weight: 600;
    font-size: 34px; line-height: 1;
    color: var(--brand-red);
  }

  .back__photo {
    position: absolute; inset: 0;
    background: linear-gradient(180deg, var(--card-red-top) 0%, #d8303a 45%, var(--card-red-bottom) 100%);
  }
  .person {
    position: absolute; left: 65px; top: 195px;
    font-family: "Open Sans", sans-serif;
  }
  .person__name {
    color: var(--gold); font-weight: 700; font-size: 29px; line-height: 1.1;
  }
  .person__role {
    color: var(--white); font-weight: 600; font-size: 23px; line-height: 1.3;
    letter-spacing: 0.3px;
  }
  .divider {
    position: absolute; left: 404px; top: 152px; width: 2px; height: 147px;
    background: var(--white);
  }
  .contacts {
    position: absolute; left: 437px; top: 139px; list-style: none;
    font-family: "Source Sans 3", sans-serif; color: var(--white);
  }
  .contacts li {
    display: flex; align-items: center; height: 42px;
    font-size: 20px; letter-spacing: 1.2px;
  }
  .contacts li.address { letter-spacing: 0.2px; }
  .contacts li.phone { letter-spacing: 2px; }
  .contacts svg {
    width: 26px; height: 26px; margin-right: 15px; flex: none;
    fill: none; stroke: var(--gold); stroke-width: 1.6;
    stroke-linecap: round; stroke-linejoin: round;
  }
</style>
</head>
<body>
<main class="sheet">

  <section class="card card--front">
    <div class="front__photo" role="img" aria-label="Black and white photo of a small gabled farmhouse with a grass roof on open moorland with mountains beyond"></div>
    <p class="company-name">Ember Realty Inc</p>
  </section>

  <section class="card card--back">
    <div class="back__photo" role="img" aria-label="Red-toned photo of the same farmhouse on open moorland"></div>

    <div class="person">
      <p class="person__name">Daniel R. Whitmore</p>
      <p class="person__role">Managing Director</p>
    </div>

    <div class="divider"></div>

    <ul class="contacts">
      <li class="phone">
        <svg viewBox="0 0 24 24" aria-hidden="true"><path fill="var(--gold)" stroke="none" d="M6.6 2.5c.6-.4 1.4-.2 1.8.4l2 3.2c.4.6.2 1.3-.3 1.7L8.6 9c.9 2.4 3.6 5.1 6.3 6.4l1.3-1.5c.4-.5 1.2-.6 1.7-.3l3.3 2c.6.4.8 1.2.4 1.8l-1.2 1.9c-.6.9-1.8 1.4-2.9 1.1C11 18.8 5.2 13 3.6 7.2c-.3-1.1.1-2.3 1.1-2.9z"/></svg>
        555 - 203 - 4187
      </li>
      <li>
        <svg viewBox="0 0 24 24" aria-hidden="true"><circle cx="12" cy="12" r="10"/><ellipse cx="12" cy="12" rx="4.5" ry="10"/><path d="M2 12h20"/></svg>
        www.emberre.com
      </li>
      <li>
        <svg viewBox="0 0 24 24" aria-hidden="true"><path d="M22 3 2 10.5l7.5 3L22 3zM9.5 13.5 12 21l10-18M9.5 13.5V19"/></svg>
        info@emberre.com
      </li>
      <li class="address">
        <svg viewBox="0 0 24 24" aria-hidden="true"><path d="M12 22s-7-7.2-7-12.5a7 7 0 0 1 14 0C19 14.8 12 22 12 22z"/><circle cx="12" cy="9.5" r="2.6"/></svg>
        48 Harbor Ln. Fairview MA 02190
      </li>
    </ul>
  </section>

</main>
</body>
</html>
```